Velk Partners Building Business Cards

We need a business card that reflects our business as "Solar Experts" in San Diego. Browse our website www.velkpartners.example our License needs to be displayed as "CSLB# 3867140" our phone number is (619) 555-0187

Save thousands on your electric bills and increase the value of your home while helping to protect the environment. Our solar installation experts will help you design the system that's right for you, using only the highest quality equipment that will look great and give you ideal performance. Our goal is to make you energy independent, and get your electric bill to 0.

Paul Osterby
(619) 555-0187
paul@velkpartners.example

Target Market(s)

Home owners in san diego looking for solar

Industry/Entity Type

Solar Energy

Contact Information for Business Card

Paul Osterby
(619) 555-0187
paul@velkpartners.example

Font styles to use
Other font styles liked:
• Use our logo font

Requirements
Must have
• License needs to be displayed as "CSLB# 3867140" our phone number is (619) 555-0187
Nice to have
• Real images of rooftop home solar in san diego
Should not have
• our business address

```html
<!DOCTYPE html>
<html lang="en">
<head>
<meta charset="utf-8">
<title>Velk Partners Building – Business Cards</title>
<link rel="stylesheet" href="https://fonts.googleapis.com/css2?family=Poppins:wght@700&family=Tinos:wght@400&display=swap">
<style>
  :root {
    --brand-blue: #1f4fa3;
    --deep-blue: #173f8a;
    --sun-yellow: #f2c518;
    --paper: #ffffff;
    --backdrop: #e9e6e1;
    --ink-light: #ffffff;
  }
  * { box-sizing: border-box; margin: 0; padding: 0; }
  html, body { width: 1200px; height: 780px; overflow: hidden; }
  body {
    background: var(--backdrop);
    display: flex;
    align-items: center;
    justify-content: center;
    gap: 40px;
  }
  .card {
    position: relative;
    width: 540px;
    height: 309px;
    border-radius: 4px;
    overflow: hidden;
    box-shadow: 0 6px 18px rgba(0,0,0,0.18);
  }
  .card-front { background: var(--paper); }
  .card-front .wave { position: absolute; inset: 0; width: 100%; height: 100%; }
  .brand-name {
    font-family: "Poppins", sans-serif;
    font-weight: 700;
    line-height: 1.05;
  }
  .card-front .brand-name {
    position: absolute;
    left: 34px;
    top: 78px;
    font-size: 34px;
    color: var(--brand-blue);
  }
  .holder-name {
    position: absolute;
    left: 36px;
    top: 196px;
    font-family: "Tinos", serif;
    font-size: 19px;
    color: var(--brand-blue);
  }
  .contact {
    position: absolute;
    right: 60px;
    top: 34px;
    list-style: none;
    font-family: "Tinos", serif;
    font-size: 14px;
    line-height: 22px;
    color: var(--ink-light);
    text-align: right;
  }
  .contact-icons {
    position: absolute;
    right: 22px;
    top: 38px;
    display: flex;
    flex-direction: column;
    gap: 4px;
  }
  .contact-icons svg { width: 18px; height: 18px; display: block; }
  .card-back { background: var(--deep-blue); }
  .rooftop-photo {
    position: absolute;
    inset: 0;
    background: linear-gradient(135deg, #8a9aa3 0%, #5f7d5a 22%, #2a4c9e 45%, #2c52a8 70%, #4a4d55 100%);
  }
  .card-back .brand-name {
    position: absolute;
    left: 0; right: 0;
    top: 50%;
    transform: translateY(-50%);
    text-align: center;
    font-size: 40px;
    color: var(--ink-light);
  }
</style>
</head>
<body>
  <section class="card card-front">
    <svg class="wave" viewBox="0 0 540 309" preserveAspectRatio="none" aria-hidden="true">
      <path d="M318,0 C236,70 330,196 160,309 L540,309 L540,0 Z" fill="var(--brand-blue)"/>
      <path d="M300,40 C250,110 300,210 188,300 C290,230 270,140 300,40 Z" fill="var(--paper)"/>
      <path d="M262,150 C272,220 230,270 150,309 L172,309 C252,270 280,220 262,150 Z" fill="var(--sun-yellow)"/>
    </svg>
    <h1 class="brand-name">Velk Partners<br>Building</h1>
    <p class="holder-name">Paul Osterby</p>
    <ul class="contact">
      <li>CSLB# 3867140</li>
      <li>(619) 555-0187</li>
      <li>paul@velkpartners.example</li>
      <li>www.velkpartners.example</li>
    </ul>
    <div class="contact-icons" aria-hidden="true">
      <svg viewBox="0 0 18 18"><rect width="18" height="18" fill="var(--sun-yellow)"/><path d="M5 4l2 0 1 3-1.5 1a6 6 0 0 0 3.5 3.5l1-1.5 3 1 0 2a1.5 1.5 0 0 1-1.5 1.5A9 9 0 0 1 3.5 5.5 1.5 1.5 0 0 1 5 4z" fill="var(--brand-blue)"/></svg>
      <svg viewBox="0 0 18 18"><rect width="18" height="18" fill="var(--sun-yellow)"/><rect x="3.5" y="5" width="11" height="8" fill="none" stroke="var(--brand-blue)" stroke-width="1.4"/><path d="M3.5 5l5.5 4.5 5.5-4.5" fill="none" stroke="var(--brand-blue)" stroke-width="1.4"/></svg>
      <svg viewBox="0 0 18 18"><rect width="18" height="18" fill="var(--sun-yellow)"/><circle cx="9" cy="9" r="5.5" fill="none" stroke="var(--brand-blue)" stroke-width="1.3"/><path d="M3.5 9h11M9 3.5c-2.5 3-2.5 8 0 11M9 3.5c2.5 3 2.5 8 0 11" fill="none" stroke="var(--brand-blue)" stroke-width="1.1"/></svg>
    </div>
  </section>

  <section class="card card-back">
    <div class="rooftop-photo" role="img" aria-label="Photo of solar panels installed on a San Diego home rooftop"></div>
    <h2 class="brand-name">Velk Partners<br>Building</h2>
  </section>
</body>
</html>
```